Menu Design Project

Menu design for a Japanese fast food restaurant featuring Teppanyaki and Sushi. The restaurant main scene color is black and wood color. No Japan scenery pictures. Menu try to be simply and elegant . Pictures provided can be used accordingly to the menu items, but doesn't have to be due to the back ground color of the picture is white.

Target Market(s)

Young and progressive consumers

Industry/Entity Type

Asian Restaurant

Font styles to use
Other font styles liked:
• Han Wang Kan Tan Font

Colors
1b1b1b
fee18a

Requirements
Must have
• Pictures of the Sushi that is provided, and all the item in the Word file.
Nice to have
• Keep it simple but different
Should not have
• No scenery pictures, no cherry blossom.

```html
<!DOCTYPE html>
<html lang="en">
<head>
<meta charset="utf-8">
<title>Sushi Menu</title>
<link href="https://fonts.googleapis.com/css2?family=Anton&family=PT+Sans:wght@400;700&display=swap" rel="stylesheet">
<style>
:root{
  --ink:#1b1b1b;
  --cream:#fee18a;
  --paper:#ffffff;
  --salmon:#f58a5a;
  --tuna:#d9353f;
  --rice:#efece4;
  --tempura:#f2c23a;
  --nori:#2f3a2c;
}
*{margin:0;padding:0;box-sizing:border-box}
html,body{width:1200px;height:928px;overflow:hidden;background:var(--cream)}
.menu{position:relative;width:1300px;height:1005px;transform:scale(0.9231);transform-origin:0 0;font-family:"PT Sans",Arial,sans-serif;color:var(--paper)}
.backdrop{position:absolute;inset:0}
.band{position:absolute;background:var(--cream);color:var(--ink);font-family:"Anton",Impact,sans-serif;text-align:center;line-height:1}
.abs{position:absolute;white-space:nowrap}
.name{font-weight:700;font-size:17px;line-height:1.1;text-transform:uppercase}
.name small{font-weight:400;font-size:14px;text-transform:none}
.desc{font-size:13.5px;line-height:18px}
.price{font-weight:700;font-size:13.5px}
.price-sm{font-size:12.5px;font-weight:700;line-height:18px}
.heading{font-weight:700;font-size:23px;line-height:1}
.photo{position:absolute;border-radius:10px}
</style>
</head>
<body>
<div class="menu">
  <svg class="backdrop" width="1300" height="1005" viewBox="0 0 1300 1005" aria-hidden="true">
    <polygon fill="#1b1b1b" points="0,45 440,28 1010,0 1300,0 1300,640 1300,1005 940,1005 870,975 440,970 0,955"/>
    <polygon fill="#fee18a" points="1010,0 1300,0 1300,168 1240,164"/>
    <polygon fill="#fee18a" points="890,760 1300,640 1300,1005 950,1005"/>
  </svg>

  <!-- Appetizer -->
  <div class="band" style="left:0;top:57px;width:435px;height:47px;font-size:36px;padding-top:5px">APPETIZER</div>
  <div class="abs name" style="left:29px;top:112px">Seaweed Salad</div>
  <div class="abs desc" style="left:29px;top:128px">seasoned seaweed</div>
  <div class="abs price" style="left:384px;top:130px">$2.99</div>
  <div class="abs name" style="left:29px;top:150px">Kani Salad Spicy or Non-Spicy</div>
  <div class="abs desc" style="left:29px;top:166px">crab meat, cucumber, lettuce with dressing</div>
  <div class="abs price" style="left:384px;top:168px">$3.99</div>
  <div class="abs name" style="left:29px;top:210px">Tempura Shrimp</div>
  <div class="abs desc" style="left:29px;top:226px">4 Pieces Fried Tempura Shrimp</div>
  <div class="abs price" style="left:384px;top:228px">$5.99</div>
  <div class="photo" role="img" aria-label="Fried tempura shrimp" style="left:266px;top:196px;width:92px;height:80px;background:linear-gradient(160deg,var(--tempura),#c98a1c)"></div>
  <div class="abs name" style="left:29px;top:292px">Fried Gyoza <small>(6pcs)</small></div>
  <div class="abs price" style="left:384px;top:293px">$3.99</div>
  <div class="abs name" style="left:29px;top:314px">Spring Roll <small>(4pcs)</small></div>
  <div class="abs price" style="left:384px;top:315px">$2.59</div>
  <div class="abs name" style="left:29px;top:337px">Crab Rangoon <small>(5pcs)</small></div>
  <div class="abs price" style="left:384px;top:338px">$4.50</div>

  <!-- Sashimi -->
  <div class="band" style="left:0;top:368px;width:435px;height:47px;font-size:36px;padding-top:5px">SASHIMI</div>
  <div class="abs desc" style="left:29px;top:432px;font-size:14px">*Salmon, *Tuna, *Yellow Tail,<br>*Red Snapper, *White Tuna,<br>Surf Clam</div>
  <div class="photo" role="img" aria-label="Assorted sashimi slices" style="left:224px;top:428px;width:210px;height:54px;background:linear-gradient(90deg,var(--salmon),var(--tuna) 50%,#f6e3c0)"></div>

  <!-- Nigiri -->
  <div class="band" style="left:0;top:500px;width:435px;height:47px;font-size:36px;padding-top:5px">SUSHI NIGIRI</div>
  <div class="abs desc" style="left:29px;top:559px;font-size:14px;line-height:16.5px">*Salmon, *Tuna, *Yellow Tail,<br>*Red Snapper, *White Tuna,<br>Surf Clam, Grill Eel, Ebi Shrimp,<br>Kani crab meat</div>
  <div class="photo" role="img" aria-label="Three pieces of nigiri sushi" style="left:248px;top:556px;width:185px;height:52px;background:linear-gradient(90deg,var(--tuna),#f6c2b4 50%,var(--salmon))"></div>
  <div class="abs desc" style="left:286px;top:607px;font-size:14px">5 pieces for <b>$5.99</b></div>

  <!-- Hand roll -->
  <div class="band" style="left:0;top:636px;width:435px;height:77px;font-size:36px;padding-top:6px;line-height:0.95">HAND ROLL BUILD YOUR<br>OWN:</div>
  <div class="abs name" style="left:29px;top:726px">Pick One Protein:</div>
  <div class="abs desc" style="left:29px;top:743px;font-size:14px;line-height:16.5px">*Salmon, *Tuna, *Yellow Tail, *Red Snapper,<br>*White Tuna, Surf Clam, Grill Eel, Ebi Shrimp,<br>Kani crab meat</div>
  <div class="abs name" style="left:29px;top:796px">Pick Two Vegetable:</div>
  <div class="abs desc" style="left:29px;top:814px;font-size:14px;line-height:16.5px">Cucumber, Avocado, Lettuce, Oshigo,<br>Asparagus, Seaweed</div>
  <div class="abs name" style="left:29px;top:851px">Pick Sauce:</div>
  <div class="abs desc" style="left:29px;top:868px;font-size:14px;line-height:16.5px">Spicy Mayonnaise, Honey Wasabi,<br>Honey Mayonnaise, Unagi Sauce</div>
  <div class="photo" role="img" aria-label="Seaweed hand roll cone" style="left:333px;top:728px;width:76px;height:148px;background:linear-gradient(180deg,#6f8f45,var(--nori) 45%,#262a24)"></div>
  <div class="abs desc" style="left:345px;top:879px;font-size:14px">2 for<b>$5.99</b></div>

  <!-- Sushi -->
  <div class="band" style="left:437px;top:32px;width:435px;height:48px;font-size:36px;padding-top:5px">SUSHI</div>
  <div class="abs desc" style="left:545px;top:90px;font-size:16px">Ingredients subject to availability</div>
  <div class="abs heading" style="left:454px;top:117px">SPECIAL ROLL</div>

  <div class="abs name" style="left:454px;top:144px">Dragon Roll</div>
  <div class="abs desc" style="left:454px;top:162px">Grilled Eel fish &amp; cucumber top with<br>avocado &amp; Unagi sauce</div>
  <div class="abs price" style="left:808px;top:181px">$9.99</div>
  <div class="abs name" style="left:454px;top:201px">Deluxe Black Dragon Roll</div>
  <div class="abs desc" style="left:454px;top:219px">Tempura Shrimp top with Avocado,<br>Grilled Eel fish &amp; Unagi sacue</div>
  <div class="abs price" style="left:808px;top:238px">$11.99</div>
  <div class="abs name" style="left:454px;top:258px">Rainbow Roll</div>
  <div class="abs desc" style="left:454px;top:276px">avocado, cucumber &amp; Kani top with red<br>snapper, tuna, salmon&amp;avocado</div>
  <div class="abs price" style="left:808px;top:295px">$10.99</div>
  <div class="abs name" style="left:454px;top:316px">Four Season Roll</div>
  <div class="abs desc" style="left:454px;top:334px">Tuna, salmon, oshinko</div>
  <div class="abs price" style="left:808px;top:335px">$9.99</div>
  <div class="abs name" style="left:454px;top:355px">Deluxe Philly Roll</div>
  <div class="abs desc" style="left:454px;top:373px">Salmon, cream cheese &amp; avocado top<br>with more salmon</div>
  <div class="abs price" style="left:808px;top:392px">$9.9</div>
  <div class="abs name" style="left:454px;top:412px">Massago Roll</div>
  <div class="abs desc" style="left:454px;top:430px">Kani crab meat, cucumber &amp; avocado top<br>with Premium Massago Roe</div>
  <div class="abs price" style="left:808px;top:449px">$8.99</div>
  <div class="abs name" style="left:454px;top:470px">Deluxe Spicy Tuna Roll</div>
  <div class="abs desc" style="left:454px;top:488px">Kani crab meat, Cucumber &amp; avocado top<br>with Spicy grounded tuna</div>
  <div class="abs price" style="left:808px;top:507px">$9.49</div>
  <div class="abs name" style="left:454px;top:527px">Deluxe Spicy Kani Roll</div>
  <div class="abs desc" style="left:454px;top:545px">Kani crab meat, cucumber &amp; avocado top<br>with seasoned ground Crab meat</div>
  <div class="abs price" style="left:808px;top:564px">$9.49</div>
  <div class="abs name" style="left:454px;top:584px">Deluxe Kani Roll</div>
  <div class="abs desc" style="left:454px;top:602px">Kani crab meat, cucumber &amp; avocado top<br>with Kani &amp; Panko crumb</div>
  <div class="abs price" style="left:808px;top:621px">$9.49</div>
  <div class="abs name" style="left:454px;top:641px">Tri Deluxe Fish Roll</div>
  <div class="abs desc" style="left:454px;top:659px">Tuna, salmon &amp; red snapper</div>
  <div class="abs price" style="left:808px;top:660px">$9.99</div>
  <div class="abs name" style="left:454px;top:680px">Sumo Roll</div>
  <div class="abs desc" style="left:454px;top:698px">Tuna, Salmon, White Tuan, Red snapper<br>Avocado &amp; Kani Crab Meat</div>
  <div class="abs price" style="left:808px;top:717px">$10.99</div>
  <div class="abs name" style="left:454px;top:737px">Hamachi Asparagus Roll</div>
  <div class="abs desc" style="left:454px;top:755px">Hamachi, Scallion &amp; Asparagus with Ponzu Sauce</div>
  <div class="abs price" style="left:808px;top:756px">$7.99</div>

  <div class="photo" role="img" aria-label="Dragon roll with avocado" style="left:703px;top:142px;width:98px;height:58px;background:linear-gradient(135deg,#8fae3c,#3d4a22)"></div>
  <div class="photo" role="img" aria-label="Black dragon roll slices" style="left:707px;top:222px;width:92px;height:40px;background:linear-gradient(90deg,var(--rice),#b7cf80)"></div>
  <div class="photo" role="img" aria-label="Rainbow roll slices" style="left:707px;top:282px;width:92px;height:36px;background:linear-gradient(90deg,var(--salmon),var(--tuna))"></div>
  <div class="photo" role="img" aria-label="Deluxe philly roll" style="left:715px;top:380px;width:85px;height:44px;background:linear-gradient(90deg,var(--salmon),var(--rice))"></div>
  <div class="photo" role="img" aria-label="Massago roll" style="left:715px;top:436px;width:87px;height:42px;background:linear-gradient(90deg,#f07a3a,var(--rice))"></div>
  <div class="photo" role="img" aria-label="Spicy tuna roll" style="left:717px;top:494px;width:85px;height:42px;background:linear-gradient(90deg,#e9a070,var(--rice))"></div>
  <div class="photo" role="img" aria-label="Spicy kani roll" style="left:717px;top:551px;width:85px;height:44px;background:linear-gradient(90deg,#efb78a,var(--rice))"></div>
  <div class="photo" role="img" aria-label="Kani roll piece" style="left:745px;top:610px;width:42px;height:42px;background:linear-gradient(180deg,#e9a7a0,var(--rice))"></div>

  <div class="abs heading" style="left:454px;top:779px">REGULAR MAKI ROLL</div>
  <div class="abs name" style="left:454px;top:806px">Salmon Roll</div>
  <div class="abs desc" style="left:454px;top:827px">salmon &amp; avocado</div>
  <div class="abs price-sm" style="left:715px;top:827px">(8pcs) $5.49(12pcs) $7.49</div>
  <div class="abs name" style="left:454px;top:849px">Tuna Roll</div>
  <div class="abs desc" style="left:454px;top:870px">tuna &amp; avocado</div>
  <div class="abs price-sm" style="left:715px;top:870px">(8pcs) $5.49 (12pcs) $7.49</div>
  <div class="abs name" style="left:454px;top:891px">Philly Roll</div>
  <div class="abs desc" style="left:454px;top:913px">salmon, cream cheese &amp; avocado</div>
  <div class="abs price-sm" style="left:715px;top:913px">(8pcs) $5.49 (12pcs) $7.49</div>
  <div class="abs name" style="left:454px;top:934px">California Roll</div>
  <div class="abs desc" style="left:454px;top:955px">cucumber, avocado &amp; kani crab meat</div>
  <div class="abs price-sm" style="left:715px;top:955px">(8pcs) $5.49 (12pcs) $7.49</div>

  <!-- Right column -->
  <div class="photo" role="img" aria-label="Tuna, snapper and salmon nigiri" style="left:892px;top:42px;width:385px;height:108px;border-radius:40px;background:linear-gradient(90deg,var(--tuna),#f5c4b6 45%,var(--salmon))"></div>

  <div class="abs name" style="left:877px;top:182px">Kani &amp; Cheese Roll</div>
  <div class="abs desc" style="left:877px;top:200px">Kani crab meat &amp; cream cheese</div>
  <div class="abs price-sm" style="left:1172px;top:183px">(8pcs) $5.49<br>(12pcs) $7.49</div>
  <div class="abs name" style="left:877px;top:231px">Shrimp Tempura Roll</div>
  <div class="abs desc" style="left:877px;top:249px">Fried tempura shrimp &amp; cucumber</div>
  <div class="abs price-sm" style="left:1172px;top:250px">(8pcs) $6.49</div>
  <div class="abs name" style="left:877px;top:280px">Alaska Roll</div>
  <div class="abs desc" style="left:877px;top:298px">Salmon &amp; avocado with massago</div>
  <div class="abs price-sm" style="left:1172px;top:281px">(8pcs) $5.49<br>(12pcs) $7.49</div>
  <div class="photo" role="img" aria-label="Alaska roll piece" style="left:1094px;top:266px;width:66px;height:74px;background:linear-gradient(180deg,#f07a3a,var(--rice))"></div>
  <div class="abs name" style="left:877px;top:330px">Grilled Eel Roll</div>
  <div class="abs desc" style="left:877px;top:348px">Eel &amp; avocado</div>
  <div class="abs price-sm" style="left:1172px;top:331px">(8pcs) $5.49<br>(12pcs) $7.49</div>
  <div class="abs name" style="left:877px;top:379px">Spicy Tuna Roll</div>
  <div class="abs desc" style="left:877px;top:397px">seasoned ground tuna</div>
  <div class="abs price-sm" style="left:1172px;top:380px">(8pcs) $5.49<br>(12pcs) $7.49</div>
  <div class="abs name" style="left:877px;top:428px">Spicy Salmon Roll</div>
  <div class="abs desc" style="left:877px;top:446px">seasoned ground salmon</div>
  <div class="abs price-sm" style="left:1172px;top:429px">(8pcs) $5.49<br>(12pcs) $7.49</div>
  <div class="abs name" style="left:877px;top:477px">Spicy Kani Roll</div>
  <div class="abs desc" style="left:877px;top:495px">seasoned ground crab meat</div>
  <div class="abs price-sm" style="left:1172px;top:478px">(8pcs) $5.49<br>(12pcs) $7.49</div>
  <div class="abs name" style="left:877px;top:527px">Vegetarian Roll</div>
  <div class="abs desc" style="left:877px;top:545px">avocado, cucumber</div>
  <div class="abs price-sm" style="left:1172px;top:528px">(8pcs) $4.49<br>(16pcs) $7.99</div>
  <div class="abs name" style="left:877px;top:594px;line-height:25px">Add Ajitsuke Seasoned Fried Bean Curd<br>for $1.00 more</div>

  <div class="photo" role="img" aria-label="Close-up of a maki roll with salmon, cream cheese and avocado" style="left:945px;top:670px;width:310px;height:288px;border-radius:40px;background:linear-gradient(160deg,#ece8dc,#d9d3c4)"></div>
</div>
</body>
</html>
```